Simple, High-Class Web Design Wanted - Motivational Speakers Site

1. Full Brief/Request & Specs outlined on following video -
http://clipvault-demo.com/watch/rTkWmaPzQb

2. Use colours, images as you feel suits objective (we are happy to pay up to US$30 for any good images but must have licence/permission).

3. Layout probably similar to existing site - www.podiumtalentgroup.com.au / http://podiumtalentgroup.com.au/contact.php

4. Must Be Able to Coded for MOBILE-FRIENDLINESS & WordPress friendly Ideal.

5. This is the first, small job of many we/graphic design jobs. If suits, winning designer may be offered all future work direct.

Thanks & look forward to your design. Glen.

Target Market(s)

corporates - high end

Number of Pages Required

2 page

Font styles to use
Sans Serif

Requirements
Must have
• Classy professional look
Nice to have
• all in Video in brief
Should not have
• too many images / new images I haven't approved

```html
<!DOCTYPE html>
<html lang="en">
<head>
<meta charset="utf-8">
<title>Speaker Suggestions / Speaker Help – Keynote Circle Speakers</title>
<link href="https://fonts.googleapis.com/css2?family=Open+Sans:wght@400;600;700;800&family=Tinos&display=swap" rel="stylesheet">
<style>
  :root{
    --ink:#1e4b57;
    --green:#6aa82f;
    --band:#3a3a3a;
    --text:#4a4a4a;
    --muted:#8a8a8a;
    --required:#d8502f;
    --field-border:#c9c9c9;
    --field-bg:#ffffff;
    --footer-bg:#ececec;
    --page:#ffffff;
  }
  *{box-sizing:border-box;margin:0;padding:0}
  html,body{width:835px;height:1200px;overflow:hidden;background:var(--page)}
  body{font-family:"Open Sans",Arial,sans-serif;color:var(--text);position:relative}

  .hero{position:absolute;left:22px;top:14px}
  .hero-title{font-size:50px;font-weight:800;color:var(--ink);letter-spacing:.6px;line-height:1.05;text-transform:uppercase;white-space:nowrap}
  .hero-sub{margin-top:0;font-size:29px;font-weight:800;color:var(--green);text-transform:uppercase;line-height:1.1;white-space:nowrap}
  .hero-sub .service{color:var(--ink);font-size:19px;font-weight:700;margin-left:8px}

  .section-band{position:absolute;left:14px;right:14px;top:100px;height:50px;background:var(--band);
    color:#fff;font-family:"Tinos","Times New Roman",serif;font-size:23px;font-weight:400;letter-spacing:1.2px;
    text-align:center;line-height:50px}

  .intro-note{position:absolute;left:22px;right:22px;top:161px;font-size:8.5px;line-height:1.5;color:var(--text)}
  .intro-note b{color:var(--green)}

  .required-note{position:absolute;left:190px;top:217px;font-size:10px;font-weight:600;color:var(--required)}

  .row{position:absolute;left:0;width:835px;display:flex;align-items:center;height:18px}
  .row label{width:160px;text-align:right;padding-right:12px;font-size:8.5px;color:var(--text);line-height:1.3}
  .row label .star{color:var(--required)}
  .field{height:18px;width:318px;border:1px solid var(--field-border);background:var(--field-bg);font-size:7.5px;color:var(--muted);
    padding:0 6px;display:flex;align-items:center;justify-content:space-between;flex:none}
  .field.short{width:78px}
  .field.tall{height:22px}
  .field.area{height:70px}
  .row.tall-row{height:22px}
  .row.area-row{height:70px}
  .caret{width:0;height:0;border-left:4px solid transparent;border-right:4px solid transparent;border-top:5px solid #777}
  .inline-label{font-size:8.5px;width:79px;text-align:right;padding-right:6px}
  .inline-label .star{color:var(--required)}
  .hint{position:absolute;left:176px;font-size:7px;color:var(--muted)}
  .phone-split{display:flex;align-items:center;gap:5px}
  .phone-split .dash{font-size:9px}

  .submit{position:absolute;left:292px;top:1084px;width:66px;height:23px;background:var(--green);color:#fff;border:none;
    font-family:"Open Sans",sans-serif;font-size:9.5px;font-weight:600}

  .site-footer{position:absolute;left:0;right:0;top:1160px;height:40px;background:var(--footer-bg)}
  .site-footer p{text-align:center;font-size:7.5px;color:var(--text);line-height:40px}
  .page-no{position:absolute;right:22px;top:0;font-size:8.5px;line-height:40px;color:var(--text)}
</style>
</head>
<body>
  <header class="hero">
    <h1 class="hero-title">Find the speaker for your</h1>
    <p class="hero-sub">Next event here ... <span class="service">FREE INDUSTRY SERVICE</span></p>
  </header>

  <h2 class="section-band">SPEAKER SUGGESTIONS / SPEAKER HELP</h2>

  <p class="intro-note"><b>Note:</b> The information you provide on this form is only seen by our speaker team to help with your enquiry. It will be treated only as an enquiry directly; no obligation is incurred and we do not share your contact details with anyone.</p>

  <p class="required-note">* Required Fields (just helps refine the suggestions)</p>

  <form class="enquiry-form">
    <div class="row" style="top:266px"><label>Subject <span class="star">*</span></label><div class="field">Select Subject<span class="caret"></span></div></div>
    <div class="row" style="top:291px"><label>Company/Group <span class="star">*</span></label><div class="field"></div></div>
    <div class="row" style="top:317px"><label>City/area the talk will be in <span class="star">*</span></label><div class="field"></div></div>
    <div class="row" style="top:340px"><label>State <span class="star">*</span></label><div class="field short">Select<span class="caret"></span></div><span class="inline-label">Country <span class="star">*</span></span><div class="field short">Australia<span class="caret"></span></div></div>
    <div class="row tall-row" style="top:376px"><label>The specific information /<br>Type of Speaker Preferred (etc) <span class="star">*</span></label><div class="field tall"></div></div>

    <div class="row" style="top:492px"><label>First Name <span class="star">*</span></label><div class="field"></div></div>
    <div class="row" style="top:520px"><label>Last Name</label><div class="field"></div></div>
    <div class="row" style="top:549px"><label>Phone (Business)</label><div class="phone-split"><div class="field short"></div><span class="dash">–</span><div class="field" style="width:150px"></div></div></div>
    <span class="hint" style="top:578px">Note: can be used if any problem with email.</span>
    <div class="row" style="top:600px"><label>Phone (Mobile)</label><div class="field"></div></div>
    <div class="row" style="top:628px"><label>Email <span class="star">*</span></label><div class="field"></div></div>
    <div class="row" style="top:653px"><label>Approximate Budget</label><div class="field">Select Approximate Budget<span class="caret"></span></div></div>
    <div class="row" style="top:679px"><label>Nature of Talk/Desired Purpose</label><div class="field"></div></div>
    <div class="row" style="top:704px"><label>Type of Attendees</label><div class="field"></div></div>
    <span class="hint" style="top:731px">e.g. executives, self-employed, employees, mixed etc</span>
    <div class="row" style="top:755px"><label>Expected Numbers</label><div class="field"></div></div>
    <div class="row" style="top:781px"><label>Duration of Talk</label><div class="field"></div></div>
    <div class="row" style="top:806px"><label>Talk Date</label><div class="field"></div></div>
    <span class="hint" style="top:833px">Or Date looking at</span>
    <div class="row area-row" style="top:862px"><label>Further Comments/Queries</label><div class="field area"></div></div>

    <button type="button" class="submit">Submit</button>
  </form>

  <footer class="site-footer">
    <p>© 2015, Keynote Circle Speakers. All Rights Reserved</p>
    <span class="page-no">02</span>
  </footer>
</body>
</html>
```